web page look and feel - B2B enterprise application

We have an enterprise application with 10 to 15 core pages and several supporting pages or popups. To start, we want the graphical design of the Users, Roles and Data Source pages and their supporting popups, wizards, etc. to be made beautiful. That is around 10 pages in total. There is a fair amount of redundancy among the pages. I have attached 5 screenshots. We very much want the pages to project a premium feel. That is absolutely essential. The color scheme is blue and sometimes yellow (only if it makes the page look better) plus black, gray and white. If the design of these screens goes well, we would expand the project to continue with other pages. The core of what we are looking for is graphic in nature but we are open to workflow suggestions if you have them. The Roles screen needs some improvements to the layout. I am looking for everything that includes icons, fonts, spacing, etc. I assume getting to the final design will take some back and forth with multiple revisions.

Target Market(s)

Large Enterprises

Number of Pages Required

5+ page

Requirements
Must have
• Premium feel

```html
<!DOCTYPE html>
<html lang="en">
<head>
<meta charset="utf-8">
<title>Users – Tessaly Data</title>
<link rel="stylesheet" href="https://fonts.googleapis.com/css2?family=Dosis:wght@400;500;600&family=Montserrat:wght@300;400;500&display=swap">
<style>
:root{
  --navy:#071e3b;
  --navy-line:#2a3f5c;
  --brand-a:#0d7be8;
  --brand-b:#0a2d9e;
  --blue:#2b8ef0;
  --blue-icon:#3a8ee8;
  --blue-soft:#6aaef0;
  --page:#f6f9fd;
  --white:#ffffff;
  --ink:#333a44;
  --cell:#5d6670;
  --grid:#b9d6f4;
  --side-text:#e8eef6;
  --side-muted:#aab6c6;
}
*{box-sizing:border-box;margin:0;padding:0}
html,body{width:1200px;height:786px;overflow:hidden}
body{font-family:"Dosis",sans-serif;background:var(--page);position:relative;color:var(--ink)}

.sidebar{position:absolute;left:0;top:0;width:300px;height:786px;background:var(--navy);color:var(--side-text)}
.brand{height:80px;background:linear-gradient(90deg,var(--brand-a),var(--brand-b));display:flex;align-items:center;padding-left:42px;gap:12px}
.brand-dot{width:20px;height:20px;border-radius:50%;background:var(--white)}
.brand-name{font-family:"Dosis",sans-serif;font-weight:500;font-size:26px;color:var(--white)}

.profile{display:flex;align-items:center;gap:9px;margin:20px 20px 0 40px;padding-bottom:20px}
.profile-rule{margin:0 20px;border-top:1px solid var(--navy-line)}
.avatar{width:40px;height:40px;border-radius:50%;background:linear-gradient(135deg,#c9a58c,#6b4b3a);border:2px solid #d8dde4}
.profile-name{font-family:"Montserrat",sans-serif;font-size:15px;font-weight:400}
.profile-mail{font-family:"Montserrat",sans-serif;font-size:12.5px;font-weight:300;color:var(--side-muted);margin-top:2px}

.nav{list-style:none;margin-top:15px}
.nav li{height:32px;display:flex;align-items:center;padding-left:40px;padding-right:37px;font-size:15.5px;font-weight:400}
.nav svg{width:19px;height:19px;margin-right:13px;fill:var(--white)}
.nav .chev{margin-left:auto;width:9px;height:9px;margin-right:0;fill:none;stroke:var(--white);stroke-width:1.4}

.clock{position:absolute;top:658px;left:30px;right:30px;display:flex;justify-content:space-between;font-size:15.5px;font-weight:500}
.clock span{display:flex;align-items:center;gap:10px}
.clock svg{width:26px;height:26px;fill:none;stroke:var(--white);stroke-width:2}

.topbar{position:absolute;left:300px;top:0;right:0;height:81px;background:var(--white);border-bottom:1px solid var(--blue)}
.topbar svg{position:absolute;fill:var(--blue)}
.menu{left:30px;top:31px;width:19px;height:18px}
.user-menu{position:absolute;left:742px;top:27px;display:flex;align-items:center;gap:13px;font-size:18px;font-weight:500;color:var(--blue)}
.user-menu svg{position:static}

.title{position:absolute;left:329px;top:113px;font-family:"Montserrat",sans-serif;font-weight:400;font-size:31px;color:var(--ink)}
.add{position:absolute;left:434px;top:122px;width:64px;height:27px;background:#0f72e0;border-radius:3px;color:var(--white);font-size:16px;font-weight:600;display:flex;align-items:center;justify-content:center;gap:5px;box-shadow:0 2px 8px rgba(15,114,224,.45)}
.add svg{width:14px;height:14px;fill:none;stroke:var(--white);stroke-width:1.5}
.search{position:absolute;right:30px;top:123px;display:flex;align-items:center;gap:8px;font-size:16px;color:var(--blue-soft);font-weight:500}
.search svg{width:22px;height:22px;fill:none;stroke:var(--blue);stroke-width:1.6}

.users{position:absolute;left:330px;top:188px;width:840px;border-collapse:collapse;font-size:16px}
.users th{background:var(--blue);color:var(--white);font-weight:500;height:39px;border-left:1px solid #1a6fc6;font-size:16px}
.users th:first-child{border-left:none}
.users td{height:39px;text-align:center;color:var(--cell);border:1px solid var(--grid);background:var(--white);font-weight:400}
.users .exp svg{width:11px;height:7px;fill:none;stroke:var(--blue);stroke-width:1.8}
.actions{display:flex;justify-content:center;gap:9px}
.actions svg{width:20px;height:20px}

.pager{position:absolute;left:677px;top:521px;display:flex;align-items:center;gap:8px;font-size:16px;color:var(--blue-soft)}
.pager .on{color:var(--blue);font-weight:600}
.pager svg{width:7px;height:11px;fill:none;stroke:var(--blue-soft);stroke-width:2}
.per-page{margin-left:17px;background:#76b2ef;color:var(--white);font-weight:600;padding:0 5px;height:18px;display:flex;align-items:center;gap:3px;font-size:15px}
.per-page svg{width:6px;height:4px;stroke:var(--white);stroke-width:1.4}
</style>
</head>
<body>
<aside class="sidebar">
  <div class="brand"><span class="brand-dot"></span><span class="brand-name">Tessaly Data</span></div>
  <div class="profile">
    <div class="avatar" role="img" aria-label="Profile photo of the signed-in user"></div>
    <div><div class="profile-name">Dana Reyes</div><div class="profile-mail">dana.reyes@example.com</div></div>
  </div>
  <div class="profile-rule"></div>
  <ul class="nav">
    <li><svg viewBox="0 0 20 20"><circle cx="10" cy="5.5" r="4.5"/><path d="M2 19c0-5 3.5-8 8-8s8 3 8 8z"/></svg>User<svg class="chev" viewBox="0 0 10 10"><path d="M3 1l4 4-4 4"/></svg></li>
    <li><svg viewBox="0 0 20 20"><rect x="0" y="2" width="20" height="7"/><rect x="0" y="11" width="20" height="7"/><rect x="2" y="4.5" width="2" height="2" fill="#071e3b"/><rect x="2" y="13.5" width="2" height="2" fill="#071e3b"/></svg>Data Source<svg class="chev" viewBox="0 0 10 10"><path d="M3 1l4 4-4 4"/></svg></li>
    <li><svg viewBox="0 0 20 20"><rect x="0" y="0" width="9" height="20"/><rect x="11" y="0" width="9" height="9"/><rect x="11" y="11" width="9" height="9"/></svg>Data Sets</li>
    <li><svg viewBox="0 0 20 20"><rect x="0" y="0" width="8" height="20"/><rect x="10" y="1" width="10" height="3"/><rect x="10" y="6" width="10" height="3"/><rect x="10" y="11" width="10" height="3"/><rect x="10" y="16" width="10" height="3"/></svg>Rule Sets</li>
    <li><svg viewBox="0 0 20 20" style="fill:none;stroke:#fff;stroke-width:1.8"><circle cx="10" cy="10" r="8.5"/><path d="M10 5v5l3 3"/></svg>Schedule</li>
    <li><svg viewBox="0 0 20 20" style="fill:none;stroke:#fff;stroke-width:1.8"><path d="M3 9a7 7 0 0 1 13-3M17 11a7 7 0 0 1-13 3"/><path d="M16 2v4h-4M4 18v-4h4"/></svg>Metadata Import/Export<svg class="chev" viewBox="0 0 10 10"><path d="M3 1l4 4-4 4"/></svg></li>
  </ul>
  <div class="clock">
    <span><svg viewBox="0 0 26 26"><rect x="2" y="4" width="22" height="20" rx="2"/><path d="M2 9h22M7 1v5M13 1v5M19 1v5"/><text x="13" y="21" text-anchor="middle" font-size="11" font-weight="700" fill="#fff" stroke="none" font-family="Dosis,sans-serif">5</text></svg>July 05</span>
    <span><svg viewBox="0 0 26 26"><circle cx="13" cy="13" r="11"/><path d="M13 6v7l-3 4"/></svg>18:36</span>
  </div>
</aside>

<header class="topbar">
  <svg class="menu" viewBox="0 0 19 18"><rect y="1" width="19" height="3"/><rect y="7.5" width="19" height="3"/><rect y="14" width="19" height="3"/></svg>
  <svg viewBox="0 0 26 20" style="left:493px;top:30px;width:26px;height:20px"><path d="M2 17a11 11 0 0 1 22 0" fill="none" stroke="#2b8ef0" stroke-width="2.6"/><path d="M13 17l6-8" stroke="#2b8ef0" stroke-width="2.6"/></svg>
  <svg viewBox="0 0 26 26" style="left:543px;top:27px;width:26px;height:26px"><path d="M2 24L17 9" stroke="#2b8ef0" stroke-width="3"/><circle cx="21" cy="4" r="1.4"/><circle cx="24" cy="8" r="1.2"/><circle cx="17" cy="3" r="1"/></svg>
  <svg viewBox="0 0 26 26" style="left:593px;top:27px;width:26px;height:26px"><circle cx="13" cy="13" r="13"/><text x="13" y="20.5" text-anchor="middle" font-size="21" font-weight="700" fill="#fff" font-family="Dosis,sans-serif">?</text></svg>
  <svg viewBox="0 0 28 26" style="left:643px;top:27px;width:28px;height:26px"><circle cx="10" cy="10" r="6.5" fill="none" stroke="#2b8ef0" stroke-width="4"/><circle cx="10" cy="10" r="9" fill="none" stroke="#2b8ef0" stroke-width="3" stroke-dasharray="3 4"/><circle cx="21" cy="19" r="4.2" fill="none" stroke="#2b8ef0" stroke-width="3"/><circle cx="21" cy="19" r="6" fill="none" stroke="#2b8ef0" stroke-width="2.4" stroke-dasharray="2.5 3"/><circle cx="22" cy="5" r="2.6" fill="none" stroke="#2b8ef0" stroke-width="2.2"/></svg>
  <div class="user-menu">
    <svg viewBox="0 0 20 24" width="20" height="24"><circle cx="10" cy="6" r="5.5"/><path d="M0 24c0-7 4-11 10-11s10 4 10 11z"/></svg>
    Dana Reyes
    <svg viewBox="0 0 12 8" width="11" height="7" style="fill:none;stroke:#2b8ef0;stroke-width:1.4"><path d="M1 1l5 5 5-5"/></svg>
  </div>
</header>

<main>
  <h1 class="title">Users</h1>
  <div class="add"><svg viewBox="0 0 14 14"><circle cx="7" cy="7" r="6"/><path d="M7 4v6M4 7h6"/></svg>Add</div>
  <div class="search">Search <svg viewBox="0 0 22 22"><circle cx="9" cy="9" r="7.5"/><path d="M14.5 14.5l6 6"/></svg></div>

  <table class="users">
    <colgroup><col style="width:40px"><col style="width:137px"><col style="width:137px"><col style="width:137px"><col style="width:137px"><col style="width:137px"><col style="width:115px"></colgroup>
    <thead><tr><th></th><th>First Name</th><th>Last Name</th><th>Username</th><th>Email</th><th>Status</th><th>Edit</th></tr></thead>
    <tbody>
      <tr><td class="exp"><svg viewBox="0 0 12 8"><path d="M1 1l5 5 5-5"/></svg></td><td>Test</td><td>Test</td><td>test.1</td><td>test@example.com</td><td>Active</td><td><div class="actions"><svg viewBox="0 0 20 20"><rect width="20" height="20" rx="2" fill="#3a8ee8"/><path d="M6 14l1-3 6-6 2 2-6 6zM5 16h10" fill="none" stroke="#fff" stroke-width="1.2"/></svg><svg viewBox="0 0 20 20"><rect width="20" height="20" rx="2" fill="#3a8ee8"/><rect x="5" y="4" width="7" height="9" fill="none" stroke="#fff" stroke-width="1.3"/><rect x="8" y="7" width="7" height="9" fill="#3a8ee8" stroke="#fff" stroke-width="1.3"/></svg><svg viewBox="0 0 20 20"><rect width="20" height="20" rx="2" fill="#3a8ee8"/><path d="M5 6h10M8 6V4h4v2M6 6l1 10h6l1-10M9 8v6M11 8v6" fill="none" stroke="#fff" stroke-width="1.3"/></svg></div></td></tr>
      <tr><td class="exp"><svg viewBox="0 0 12 8"><path d="M1 1l5 5 5-5"/></svg></td><td>Test</td><td>Test</td><td>test.1</td><td>test@example.com</td><td>Active</td><td><div class="actions"><svg viewBox="0 0 20 20"><rect width="20" height="20" rx="2" fill="#3a8ee8"/><path d="M6 14l1-3 6-6 2 2-6 6zM5 16h10" fill="none" stroke="#fff" stroke-width="1.2"/></svg><svg viewBox="0 0 20 20"><rect width="20" height="20" rx="2" fill="#3a8ee8"/><rect x="5" y="4" width="7" height="9" fill="none" stroke="#fff" stroke-width="1.3"/><rect x="8" y="7" width="7" height="9" fill="#3a8ee8" stroke="#fff" stroke-width="1.3"/></svg><svg viewBox="0 0 20 20"><rect width="20" height="20" rx="2" fill="#3a8ee8"/><path d="M5 6h10M8 6V4h4v2M6 6l1 10h6l1-10M9 8v6M11 8v6" fill="none" stroke="#fff" stroke-width="1.3"/></svg></div></td></tr>
      <tr><td class="exp"><svg viewBox="0 0 12 8"><path d="M1 1l5 5 5-5"/></svg></td><td>Test</td><td>Test</td><td>test.1</td><td>test@example.com</td><td>Active</td><td><div class="actions"><svg viewBox="0 0 20 20"><rect width="20" height="20" rx="2" fill="#3a8ee8"/><path d="M6 14l1-3 6-6 2 2-6 6zM5 16h10" fill="none" stroke="#fff" stroke-width="1.2"/></svg><svg viewBox="0 0 20 20"><rect width="20" height="20" rx="2" fill="#3a8ee8"/><rect x="5" y="4" width="7" height="9" fill="none" stroke="#fff" stroke-width="1.3"/><rect x="8" y="7" width="7" height="9" fill="#3a8ee8" stroke="#fff" stroke-width="1.3"/></svg><svg viewBox="0 0 20 20"><rect width="20" height="20" rx="2" fill="#3a8ee8"/><path d="M5 6h10M8 6V4h4v2M6 6l1 10h6l1-10M9 8v6M11 8v6" fill="none" stroke="#fff" stroke-width="1.3"/></svg></div></td></tr>
      <tr><td class="exp"><svg viewBox="0 0 12 8"><path d="M1 1l5 5 5-5"/></svg></td><td>Test</td><td>Test</td><td>test.1</td><td>test@example.com</td><td>Active</td><td><div class="actions"><svg viewBox="0 0 20 20"><rect width="20" height="20" rx="2" fill="#3a8ee8"/><path d="M6 14l1-3 6-6 2 2-6 6zM5 16h10" fill="none" stroke="#fff" stroke-width="1.2"/></svg><svg viewBox="0 0 20 20"><rect width="20" height="20" rx="2" fill="#3a8ee8"/><rect x="5" y="4" width="7" height="9" fill="none" stroke="#fff" stroke-width="1.3"/><rect x="8" y="7" width="7" height="9" fill="#3a8ee8" stroke="#fff" stroke-width="1.3"/></svg><svg viewBox="0 0 20 20"><rect width="20" height="20" rx="2" fill="#3a8ee8"/><path d="M5 6h10M8 6V4h4v2M6 6l1 10h6l1-10M9 8v6M11 8v6" fill="none" stroke="#fff" stroke-width="1.3"/></svg></div></td></tr>
      <tr><td class="exp"><svg viewBox="0 0 12 8"><path d="M1 1l5 5 5-5"/></svg></td><td>Test</td><td>Test</td><td>test.1</td><td>test@example.com</td><td>Active</td><td><div class="actions"><svg viewBox="0 0 20 20"><rect width="20" height="20" rx="2" fill="#3a8ee8"/><path d="M6 14l1-3 6-6 2 2-6 6zM5 16h10" fill="none" stroke="#fff" stroke-width="1.2"/></svg><svg viewBox="0 0 20 20"><rect width="20" height="20" rx="2" fill="#3a8ee8"/><rect x="5" y="4" width="7" height="9" fill="none" stroke="#fff" stroke-width="1.3"/><rect x="8" y="7" width="7" height="9" fill="#3a8ee8" stroke="#fff" stroke-width="1.3"/></svg><svg viewBox="0 0 20 20"><rect width="20" height="20" rx="2" fill="#3a8ee8"/><path d="M5 6h10M8 6V4h4v2M6 6l1 10h6l1-10M9 8v6M11 8v6" fill="none" stroke="#fff" stroke-width="1.3"/></svg></div></td></tr>
      <tr><td class="exp"><svg viewBox="0 0 12 8"><path d="M1 1l5 5 5-5"/></svg></td><td>Test</td><td>Test</td><td>test.1</td><td>test@example.com</td><td>Active</td><td><div class="actions"><svg viewBox="0 0 20 20"><rect width="20" height="20" rx="2" fill="#3a8ee8"/><path d="M6 14l1-3 6-6 2 2-6 6zM5 16h10" fill="none" stroke="#fff" stroke-width="1.2"/></svg><svg viewBox="0 0 20 20"><rect width="20" height="20" rx="2" fill="#3a8ee8"/><rect x="5" y="4" width="7" height="9" fill="none" stroke="#fff" stroke-width="1.3"/><rect x="8" y="7" width="7" height="9" fill="#3a8ee8" stroke="#fff" stroke-width="1.3"/></svg><svg viewBox="0 0 20 20"><rect width="20" height="20" rx="2" fill="#3a8ee8"/><path d="M5 6h10M8 6V4h4v2M6 6l1 10h6l1-10M9 8v6M11 8v6" fill="none" stroke="#fff" stroke-width="1.3"/></svg></div></td></tr>
    </tbody>
  </table>

  <nav class="pager">
    <svg viewBox="0 0 7 11"><path d="M6 1L1.5 5.5 6 10"/></svg>
    <span class="on">1</span><span>2</span><span>3</span><span>4</span>
    <svg viewBox="0 0 7 11"><path d="M1 1l4.5 4.5L1 10"/></svg>
    <span class="per-page">20<svg viewBox="0 0 6 4" style="fill:none"><path d="M0.5 0.5L3 3l2.5-2.5"/></svg></span>
  </nav>
</main>
</body>
</html>
```